Company Mission & Values Poster

I'd like an A2 Portrait Poster displaying our company's Mission & Values.
See our website for our logo, fonts, mission & values.
https://valdintor.com.au/

Our Mission: Creating homes for abundant life
Values: Love, Thinking, Team, Zoe.

Some ideas to consider:
Mission as the Headline then
A logo for each of the 4 Values and the words

Target Market(s)

Myself & my team

Industry/Entity Type

Real Estate

Font styles to use
Other font styles liked:
• Company fonts as seen on our website

```html
<!DOCTYPE html>
<html lang="en">
<head>
<meta charset="utf-8">
<title>Valdintor – Mission &amp; Values</title>
<link href="https://fonts.googleapis.com/css2?family=Lato:wght@300;400;700&family=Marcellus&family=Open+Sans:wght@400;600;700&display=swap" rel="stylesheet">
<style>
  :root {
    --forest: #0a3a30;
    --forest-deep: #062a22;
    --ink: #333333;
    --muted: #6a6a6a;
    --paper: #ffffff;
  }
  * { box-sizing: border-box; margin: 0; padding: 0; }
  html, body { width: 881px; height: 1200px; overflow: hidden; background: var(--paper); }
  .poster { position: relative; width: 881px; height: 1200px; background: var(--paper); font-family: 'Lato', sans-serif; }

  .brand { position: absolute; top: 58px; left: 0; width: 881px; display: flex; justify-content: center; align-items: center; gap: 22px; }
  .brand-dot { width: 40px; height: 40px; border-radius: 50%; background: var(--forest); }
  .brand-name { font-family: 'Marcellus', serif; font-size: 58px; letter-spacing: 9px; color: var(--forest); line-height: 1; }

  .hero-photo { position: absolute; top: 157px; left: 0; width: 881px; height: 485px;
    background: linear-gradient(180deg, #efe5dc 0%, #e8d2bd 22%, #6f7f5f 36%, #a9b3a6 44%, #8b9470 52%, #cfc6ba 64%, #bdb8b1 100%); }

  .mission-tab { position: absolute; top: 274px; left: 473px; width: 351px; height: 56px; background: var(--paper); border-top-right-radius: 30px; }
  .mission-label { position: absolute; top: 280px; left: 501px; font-family: 'Open Sans', sans-serif; font-weight: 700; font-size: 34px; color: var(--forest); line-height: 1.2; }
  .mission-panel { position: absolute; top: 327px; left: 473px; width: 353px; height: 391px;
    background: linear-gradient(160deg, #0c4034 0%, var(--forest-deep) 60%, #0a3a30 100%); color: var(--paper); }
  .mission-headline { position: absolute; top: 28px; left: 28px; font-size: 48px; line-height: 59px; }
  .mission-headline .light { font-weight: 300; display: block; }
  .mission-headline .bold { font-weight: 700; display: block; }
  .mission-rule { display: inline-block; width: 90px; height: 2px; background: var(--paper); vertical-align: middle; margin-left: 8px; }
  .mission-copy { position: absolute; top: 257px; left: 28px; width: 305px; font-size: 12.6px; line-height: 18.5px; }

  .values-tab { position: absolute; top: 588px; left: 0; width: 354px; height: 54px; background: var(--forest); border-top-right-radius: 26px; }
  .values-label { position: absolute; top: 592px; left: 52px; font-family: 'Open Sans', sans-serif; font-weight: 700; font-size: 34px; color: var(--paper); line-height: 1.2; }

  .belief { position: absolute; top: 664px; left: 55px; font-family: 'Marcellus', serif; font-size: 31px; line-height: 41px; color: var(--ink); -webkit-text-stroke: 0.5px var(--ink); white-space: nowrap; }

  .value { position: absolute; top: 856px; width: 150px; }
  .value-icon { display: block; margin-left: -5px; }
  .value-title { font-family: 'Open Sans', sans-serif; font-weight: 600; font-size: 24px; color: var(--forest); margin-top: 8px; line-height: 1.1; }
  .value-text { font-size: 8.4px; line-height: 12px; color: var(--muted); margin-top: 8px; width: 145px; }

  .contact-band { position: absolute; top: 1118px; left: 0; width: 881px; height: 82px; background: var(--forest); color: var(--paper); display: flex; align-items: center; }
  .contact-title { position: absolute; left: 55px; font-size: 40px; font-weight: 700; }
  .contact-item { position: absolute; display: flex; align-items: center; gap: 10px; font-size: 17px; }
  .contact-phone { left: 337px; }
  .contact-mail { left: 553px; }
</style>
</head>
<body>
<main class="poster">
  <header class="brand">
    <span class="brand-dot"></span>
    <span class="brand-name">VALDINTOR</span>
  </header>

  <div class="hero-photo" role="img" aria-label="Photo of an outdoor terrace with a stone dining table and woven chairs overlooking a bay at sunset"></div>

  <div class="mission-tab"></div>
  <h2 class="mission-label">OUR MISSION</h2>
  <section class="mission-panel" role="img" aria-label="Dark green panel over a photo of lush garden plants">
    <h1 class="mission-headline">
      <span class="light">Creating</span>
      <span class="bold">Homes For</span>
      <span class="light">Abundant</span>
      <span class="light">Life.<span class="mission-rule"></span></span>
    </h1>
    <p class="mission-copy">We wholeheartedly believe that home is an extraordinary place: a haven where life unfolds in all its glory. Where we find solace, make cherished memories with loved ones, and savour the natural beauty that surrounds us.</p>
  </section>

  <div class="values-tab"></div>
  <h2 class="values-label">OUR VALUES</h2>

  <p class="belief">We Believe<br>Business Can Be A<br>Force For Good. Our Values Shape The Way We<br>Work And How We Make Decisions.</p>

  <article class="value" style="left:53px">
    <svg class="value-icon" width="118" height="116" viewBox="0 0 118 116" aria-hidden="true">
      <circle cx="59" cy="58" r="58" fill="var(--forest)"/>
      <circle cx="59" cy="58" r="50" fill="none" stroke="#fff" stroke-width="1.5"/>
      <path d="M50 70 L32 52 a9 9 0 0 1 18-10 a9 9 0 0 1 18 10 Z" fill="#fff"/>
      <path d="M68 80 L54 66 a7.5 7.5 0 0 1 14-8 a7.5 7.5 0 0 1 14 8 Z" fill="#fff" stroke="var(--forest)" stroke-width="3"/>
    </svg>
    <h3 class="value-title">Love</h3>
    <p class="value-text">Our mission is founded in our love and respect for people - those we develop for, those in our teams and those in the communities we create and operate within.</p>
  </article>

  <article class="value" style="left:268px">
    <svg class="value-icon" width="118" height="116" viewBox="0 0 118 116" aria-hidden="true">
      <circle cx="59" cy="58" r="58" fill="var(--forest)"/>
      <circle cx="59" cy="58" r="50" fill="none" stroke="#fff" stroke-width="1.5"/>
      <path d="M48 82 V72 C38 68 36 58 40 48 C44 38 56 34 66 38 C74 42 78 50 76 58 L80 64 L75 66 V74 H66 V82" fill="none" stroke="#fff" stroke-width="2.5" stroke-linejoin="round"/>
      <circle cx="63" cy="52" r="7" fill="none" stroke="#fff" stroke-width="2.5"/>
      <circle cx="63" cy="52" r="11" fill="none" stroke="#fff" stroke-width="2" stroke-dasharray="3 3"/>
    </svg>
    <h3 class="value-title">Thinking</h3>
    <p class="value-text">We believe in the power of thinking. Our rigorous and creative processes create beautifully considered solutions for our purchasers, the communities we develop within and the environment.</p>
  </article>

  <article class="value" style="left:483px">
    <svg class="value-icon" width="118" height="116" viewBox="0 0 118 116" aria-hidden="true">
      <circle cx="59" cy="58" r="58" fill="var(--forest)"/>
      <circle cx="59" cy="58" r="50" fill="none" stroke="#fff" stroke-width="1.5"/>
      <circle cx="47" cy="38" r="5" fill="#fff"/><circle cx="59" cy="34" r="6" fill="#fff"/><circle cx="71" cy="38" r="5" fill="#fff"/>
      <path d="M38 58 a9 9 0 0 1 18 0 Z M50 56 a9 10 0 0 1 18 0 Z M62 58 a9 9 0 0 1 18 0 Z" fill="#fff"/>
      <circle cx="59" cy="70" r="13" fill="none" stroke="#fff" stroke-width="5" stroke-dasharray="5 3"/>
      <circle cx="59" cy="70" r="6" fill="none" stroke="#fff" stroke-width="2.5"/>
    </svg>
    <h3 class="value-title">Team</h3>
    <p class="value-text">Property development is a team sport. We surround ourselves with the best designers and advisers. We strive to create an environment that allows them to do their best work and love doing it.</p>
  </article>

  <article class="value" style="left:690px">
    <svg class="value-icon" width="118" height="116" viewBox="0 0 118 116" aria-hidden="true">
      <circle cx="59" cy="58" r="58" fill="var(--forest)"/>
      <circle cx="59" cy="58" r="50" fill="none" stroke="#fff" stroke-width="1.5"/>
      <path d="M36 52 L58 30 L80 52 M42 47 V84 H62 M74 47 V60" fill="none" stroke="#fff" stroke-width="2.5" stroke-linejoin="round"/>
      <path d="M52 84 V64 H60 V84" fill="none" stroke="#fff" stroke-width="2.5"/>
      <path d="M54 44 L58 40 L62 44 Z" fill="#fff"/>
      <path d="M64 84 L84 64 V84 Z" fill="none" stroke="#fff" stroke-width="2.5" stroke-linejoin="round"/>
    </svg>
    <h3 class="value-title">Zoe</h3>
    <p class="value-text">Our mission is to create places for 'Zoe' - the Greek word for abundant life. We do this through exquisite design, quality construction and celebrating nature.</p>
  </article>

  <footer class="contact-band">
    <span class="contact-title">Get in touch</span>
    <span class="contact-item contact-phone">
      <svg width="28" height="28" viewBox="0 0 28 28" aria-hidden="true">
        <rect x="0" y="0" width="28" height="28" rx="9" fill="#fff"/>
        <path d="M9 7 L12 7 L13.5 11 L11.5 12.5 C12.5 15 13.5 16 15.5 16.5 L17 14.5 L21 16 V19 C21 20 20 21 19 21 C13 20.5 8 15.5 7 9 C7 8 8 7 9 7 Z" fill="var(--forest)"/>
      </svg>
      +00 123 456 78
    </span>
    <span class="contact-item contact-mail">
      <svg width="28" height="28" viewBox="0 0 28 28" aria-hidden="true">
        <rect x="0" y="0" width="28" height="28" rx="9" fill="#fff"/>
        <rect x="6" y="8.5" width="16" height="11" fill="none" stroke="var(--forest)" stroke-width="1.8"/>
        <path d="M6 8.5 L14 15 L22 8.5 M6 19.5 L12 14 M22 19.5 L16 14" fill="none" stroke="var(--forest)" stroke-width="1.5"/>
      </svg>
      companyname@valdintor.com.au
    </span>
  </footer>
</main>
</body>
</html>
```